Webdesign für neue Weinmarke
Zielgruppe
Kelchwandler ist eine neue Weinmarke. Es wird vorerst drei grundlegende Sorten geben: einen Rotwein, einen Weißwein und einen Rosé. Für diese neue Weinmarke wollen wir eine Webseite gestalten, welche die Weine ansprechend darstellt und zusätzlich den Kunden die Möglichkeit gibt, mehr Informationen über den Wein einzuholen. Die Marke Kelchwandler ist auch im Etikett an den Graf von Tressenbach angelehnt. Das Etikett zeigt den Baron, wie er auf einem Weinfass reitet – daher der Name „Kelchwandler“. Die Story, die wir mit dem Wein spielen, ist, dass die besonderen Fähigkeiten des Barons auch auf den Genuss des Kelchwandler zurückzuführen sind.
Die Zielgruppe für den Kelchwandler ist breit gefächert und schließt per se erst mal keine Personengruppe aus. Der Wein soll eher im niedrigeren Preissegment verkauft werden.
Aufgabenstellung
Es soll eine neue Webseite designt werden, die sich im Aufbau an der die Webseite http://www.velgor-example.de/#!/de/unsere-weine/sortiment orientieren kann. Zudem können für die Entwicklung kleine Animationen berücksichtigt werden, die die Seite auflockern. Das Design soll eine responsive Webseite unterstützen. Das Design soll zur Weinmarke Kelchwandler passen von der wir bisher nur das Etikett haben.

```html
<!DOCTYPE html>
<html lang="de">
<head>
<meta charset="utf-8">
<title>Kelchwandler – Rosé</title>
<link rel="stylesheet" href="https://fonts.googleapis.com/css2?family=Fira+Sans+Extra+Condensed:wght@500;600&family=Catamaran:wght@300;400;700&family=Libre+Baskerville&family=Yellowtail&display=swap">
<style>
:root{
  --canvas:#fcfaf2;
  --paper:#f7f5ee;
  --rose:#d9545a;
  --rose-dark:#b8393f;
  --ink:#2d2a28;
  --muted:#9c9892;
  --hill:#e4e1d8;
  --figure:#4a4642;
  --wine-red:#7e1c1e;
  --wine-white:#8fae2f;
  --card:#f1efe7;
  --white:#ffffff;
}
*{margin:0;padding:0;box-sizing:border-box}
html,body{width:675px;height:1200px;overflow:hidden;background:var(--canvas)}
.page{position:absolute;left:20px;top:192px;width:635px;height:816px;background:var(--paper);box-shadow:0 1px 6px rgba(0,0,0,.12);overflow:hidden;font-family:"Catamaran",sans-serif;color:var(--ink)}
.abs{position:absolute}
.brand{font-family:"Libre Baskerville",serif;font-size:13px;letter-spacing:.3px;color:var(--ink);white-space:nowrap}
.site-header .brand{left:72px;top:18px}
.main-nav{right:72px;top:22px;display:flex;gap:9px;font-size:7px;letter-spacing:.3px;white-space:nowrap}
.main-nav a{color:var(--ink);text-decoration:none}
.main-nav a.active{font-weight:700}
.hero-landscape{left:0;top:50px;width:635px;height:198px;background:linear-gradient(180deg,var(--paper) 0%,#eeebe3 55%,var(--hill) 100%)}
.hero-figure{left:125px;top:52px;width:165px;height:196px;border-radius:46% 46% 8px 8px;background:linear-gradient(180deg,#8a857f 0%,var(--figure) 60%,#5c5853 100%);opacity:.55}
.hero-bird{left:358px;top:60px;width:40px;height:30px;border-radius:50%;background:#bdb9b2;opacity:.6}
.rose-band{left:0;top:248px;width:635px;height:210px;background:var(--rose)}
.wine-title{left:72px;top:264px;font-family:"Fira Sans Extra Condensed",sans-serif;font-weight:600;font-size:22px;color:var(--white);letter-spacing:.2px;white-space:nowrap}
.info{left:72px;color:var(--white);width:195px}
.info h3{font-family:"Fira Sans Extra Condensed",sans-serif;font-weight:600;font-size:8.5px}
.info p{font-size:6.4px;line-height:9.6px;font-weight:300}
.info-char{top:304px}
.info-pair{top:365px}
.btn-order{left:72px;top:416px;width:93px;height:21px;background:var(--rose-dark);color:var(--white);font-family:"Fira Sans Extra Condensed",sans-serif;font-weight:600;font-size:8px;display:flex;align-items:center;justify-content:center;gap:7px;white-space:nowrap}
.fact{color:var(--white);width:70px}
.fact .dot{width:28px;height:28px;border-radius:50%;background:var(--rose-dark);display:flex;align-items:center;justify-content:center}
.fact h4{margin-top:5px;font-family:"Fira Sans Extra Condensed",sans-serif;font-weight:600;font-size:7.5px;white-space:nowrap}
.fact span{display:block;font-size:6.6px;font-weight:300}
.bottle-rose{left:468px;top:70px;width:74px;height:320px;border-radius:30px 30px 8px 8px / 40px 40px 8px 8px;background:linear-gradient(90deg,#c51f32,#ec3d4d 45%,#b11828);box-shadow:0 10px 18px rgba(0,0,0,.2)}
.vine-ornament{left:30px;top:458px;width:575px;height:50px;background:linear-gradient(180deg,#ebe8df,rgba(247,245,238,0))}
.section-title{left:72px;top:508px;font-family:"Yellowtail",cursive;font-size:33px;font-weight:400;color:var(--muted);white-space:nowrap}
.wine-card{top:602px;width:238px;height:96px;background:var(--card)}
.card-red{left:72px}
.card-white{left:323px}
.wine-card .bottle{position:absolute;left:13px;top:-47px;width:32px;height:137px;border-radius:14px 14px 5px 5px / 22px 22px 5px 5px}
.card-red .bottle{background:linear-gradient(90deg,#1c1417,#3a2a2f 45%,#140d10)}
.card-white .bottle{background:linear-gradient(90deg,#8a8c3a,#c4c86a 45%,#75782d)}
.wine-card h3{position:absolute;left:62px;top:10px;font-family:"Fira Sans Extra Condensed",sans-serif;font-weight:600;font-size:10px;white-space:nowrap}
.card-red h3{color:var(--wine-red)}
.card-white h3{color:var(--wine-white)}
.wine-card p{position:absolute;left:62px;top:27px;width:166px;font-size:6.3px;line-height:9.6px;font-weight:300;color:var(--ink)}
.wine-card svg{position:absolute;right:12px;bottom:8px}
.footer-bird{left:298px;top:722px;width:38px;height:30px;border-radius:50%;background:#8d8984;opacity:.5}
.footer-hills{left:0;top:760px;width:635px;height:56px;background:linear-gradient(180deg,rgba(247,245,238,0),#ebe8df)}
.site-footer .brand{left:0;width:635px;text-align:center;top:762px;font-size:13px}
.footer-links{left:0;width:635px;top:790px;display:flex;justify-content:center;gap:12px;font-size:6.6px;color:var(--ink);align-items:center;white-space:nowrap}
.footer-links .social{width:6px;height:6px;border-radius:50%;background:var(--ink)}
</style>
</head>
<body>
<div class="page">
  <header class="site-header">
    <div class="abs brand">KELCHWANDLER</div>
    <nav class="abs main-nav">
      <a href="#">HOME</a><a href="#">ROTWEIN</a><a href="#" class="active">ROSÉ</a><a href="#">WEIßWEIN</a><a href="#">REGIONEN</a><a href="#">DER BARON</a>
    </nav>
  </header>

  <div class="abs hero-landscape" role="img" aria-label="Gezeichnete Weinberglandschaft"></div>
  <div class="abs hero-figure" role="img" aria-label="Illustration des Barons mit Weinglas auf einem Fass"></div>
  <div class="abs hero-bird" role="img" aria-label="Gezeichnete Schwalbe"></div>

  <section class="abs rose-band"></section>
  <h1 class="abs wine-title">DES KELCHWANDLERS LIEBLICHER ROSÉ</h1>
  <div class="abs info info-char">
    <h3>CHARAKTERISTIK</h3>
    <p>Des Kelchwandlers lieblicher Rosé ermöglicht dem Genießer, so sagt man, eine erstaunliche Vielzahl an Dingen. Fruchtbetont und farblich intensiv half er wohl bereits dem Baron, auf einem Fass den Fluss hinabzusegeln.</p>
  </div>
  <div class="abs info info-pair">
    <h3>VERZEHREMPFEHLUNG</h3>
    <p>Hervorragend zu allen leichten und fitnessreichen Gerichten sowie zu hellen Fleischsorten.</p>
  </div>
  <a class="abs btn-order">JETZT BESTELLEN
    <svg width="9" height="7" viewBox="0 0 9 7"><path d="M0 3.5H8M5 0.5L8 3.5L5 6.5" stroke="#fff" stroke-width="1" fill="none"/></svg>
  </a>

  <div class="abs fact" style="left:310px;top:309px">
    <div class="dot"><svg width="12" height="12" viewBox="0 0 12 12"><g fill="#fff"><circle cx="4" cy="4" r="1.6"/><circle cx="7.5" cy="4" r="1.6"/><circle cx="5.8" cy="7" r="1.6"/><circle cx="3" cy="7.5" r="1.4"/><circle cx="5" cy="10" r="1.3"/></g></svg></div>
    <h4>REBSORTE</h4><span>Dornfelder</span>
  </div>
  <div class="abs fact" style="left:363px;top:309px">
    <div class="dot"><svg width="10" height="14" viewBox="0 0 10 14"><rect x="3.5" y="1" width="3" height="8" rx="1.5" fill="#fff"/><circle cx="5" cy="10.5" r="2.5" fill="#fff"/></svg></div>
    <h4>TRINKTEMPERATUR</h4><span>8-10 °C</span>
  </div>
  <div class="abs fact" style="left:310px;top:375px">
    <div class="dot"><svg width="12" height="14" viewBox="0 0 12 14"><path d="M3 1L8 0L11 4L10 9L7 13L3 12L1 7Z" fill="#fff"/></svg></div>
    <h4>HERKUNFT</h4><span>Rheinhessen</span>
  </div>
  <div class="abs fact" style="left:363px;top:375px">
    <div class="dot"><svg width="14" height="8" viewBox="0 0 14 8"><path d="M0 4C3 0 5 1 7 2C9 1 11 0 14 4C11 8 3 8 0 4Z" fill="#fff"/></svg></div>
    <h4>GESCHMACK</h4><span>lieblich</span>
  </div>

  <div class="abs bottle-rose" role="img" aria-label="Flasche Dornfelder Rosé"></div>

  <div class="abs vine-ornament" role="img" aria-label="Gezeichnete Weinranken mit Trauben"></div>
  <h2 class="abs section-title">Weitere Sorten</h2>

  <article class="abs wine-card card-red">
    <div class="bottle" role="img" aria-label="Flasche Rotwein"></div>
    <h3>KELCHWANDLER ROTWEIN</h3>
    <p>Des Kelchwandlers Pfälzer Dornfelder, ein edler Tropfen, vermag es seinem Genießer wundersame Eindrücke zu verleihen. Rubinrot, fruchtbetont und gehaltvoll ermutigte er bereits den Baron selbst, ein Fass über drei Hügel zu rollen, ohne auch nur ein Tröpfchen zu verschütten.</p>
    <svg width="9" height="7" viewBox="0 0 9 7"><path d="M0 3.5H8M5 0.5L8 3.5L5 6.5" stroke="#7e1c1e" stroke-width="1" fill="none"/></svg>
  </article>
  <article class="abs wine-card card-white">
    <div class="bottle" role="img" aria-label="Flasche Weißwein"></div>
    <h3>KELCHWANDLER WEIßWEIN</h3>
    <p>Des Kelchwandlers Pfälzer Riesling hat wahrlich wunderbare Harmonien. Sein ermunternder Schwung verleiht Genießern, wie dem Baron höchstselbst, nicht nur Anmut, sondern auch Heldengeist.</p>
    <svg width="9" height="7" viewBox="0 0 9 7"><path d="M0 3.5H8M5 0.5L8 3.5L5 6.5" stroke="#8fae2f" stroke-width="1" fill="none"/></svg>
  </article>

  <footer class="site-footer">
    <div class="abs footer-hills" role="img" aria-label="Gezeichnete Hügellinien"></div>
    <div class="abs footer-bird" role="img" aria-label="Gezeichnete Schwalbe"></div>
    <div class="abs brand">KELCHWANDLER</div>
    <div class="abs footer-links">
      <span>© 2018 Hellmark Getränke GmbH</span><span>Impressum</span><span>Datenschutz</span><span class="social"></span>
    </div>
  </footer>
</div>
</body>
</html>
```